I would like some help creating my first business cards for my new business, I am a facilitator of a course that I have created. I am currently starting the sales promotion and marketing part of my business and need some help designing the business cards. Something fairly simple would be good, the core theme of my work is in connection of women to themselves and to each other. My initial design is a tree lit up by lights, a very mother earth type of image. This is not my design however so I probably am not legally able to use the design. I don't have a logo. Could you possibly assist with this?

I would really like to have the following details on the business card:
Meg Donlan
0431 582 917
hi.meg.donlan@larkmail.example

And also the image

Target Market(s)

Women who are living in an isolated environment

Industry/Entity Type

Counsellor

Contact Information for Business Card

Meg Donlan
Facilitator
hi.meg.donlan@larkmail.example
0431 582 917

Font styles to use
Other font styles liked:
• Handwriting - Dakota

Colors
e34197
fee18a
3276b5
33a6d7
33b8a4

Requirements
Must have
• 1) My details as above
• 2) a design (picture) that represents the mother earth theme similar to the designs included in the brief
• 3) no copyright attached to the design
• 4) Colours are very important but it is difficult to describe the colour using the colour wheel. Please refer to the example of the tree that I have included in the drop box.
• 5) I must apologise that I forgot to add the business card needs to have the name of the business in gold letters please: Riverbend Circle Gatherings Collective, thank you
Nice to have
• It would be great to use the tree design that I included in the brief, this is my favourite picture but I think it is probably copyrighted. If it's not, that is the one I would like on my business cards please.

```html
<!DOCTYPE html>
<html lang="en">
<head>
<meta charset="utf-8">
<title>Meg Donlan – Business Card</title>
<link href="https://fonts.googleapis.com/css2?family=Open+Sans:wght@400;700&family=Great+Vibes&display=swap" rel="stylesheet">
<style>
  :root {
    --sky-centre: #f4fbff;
    --sky-mid: #d3eefb;
    --sky-edge: #9fd6f2;
    --blush: #f7d2e6;
    --gold: #c39a2e;
    --name-blue: #1f6fb8;
    --ink-grey: #555a60;
    --icon-blue: #6cb2e0;
    --leaf-light: #b7e27a;
    --leaf-deep: #5fbf4a;
  }
  * { margin: 0; padding: 0; box-sizing: border-box; }
  html, body {
    width: 1200px;
    height: 750px;
    overflow: hidden;
    background: #e9e9e9;
  }
  .business-card {
    position: relative;
    width: 1200px;
    height: 750px;
    overflow: hidden;
    background: radial-gradient(ellipse 70% 75% at 58% 55%, var(--sky-centre) 0%, var(--sky-mid) 50%, var(--sky-edge) 100%);
    font-family: "Open Sans", Arial, sans-serif;
  }
  .identity {
    position: absolute;
    left: 790px;
    top: 70px;
  }
  .identity .person-name {
    font-weight: 700;
    font-size: 38px;
    color: var(--name-blue);
    letter-spacing: -0.5px;
    line-height: 1;
  }
  .identity .person-role {
    margin-top: 4px;
    margin-left: 16px;
    font-size: 22px;
    color: var(--ink-grey);
  }
  .tagline {
    position: absolute;
    left: 460px;
    top: 250px;
    font-family: "Great Vibes", cursive;
    font-weight: 400;
    color: var(--gold);
    font-size: 66px;
    line-height: 1.1;
    white-space: nowrap;
  }
  .tagline .line-two {
    display: block;
    padding-left: 100px;
  }
  .tree-artwork {
    position: absolute;
    left: 110px;
    top: 250px;
    width: 320px;
    height: 360px;
    background: radial-gradient(closest-side at 50% 45%, var(--leaf-light) 0%, var(--leaf-deep) 55%, rgba(95,191,74,0.3) 85%, rgba(95,191,74,0) 100%);
  }
  .footer-band {
    position: absolute;
    left: 0;
    bottom: 0;
    width: 1200px;
    height: 88px;
    background: var(--blush);
  }
  .contact-tab {
    position: absolute;
    left: 290px;
    bottom: 0;
    width: 720px;
    height: 112px;
    border-radius: 26px 26px 0 0;
    background: linear-gradient(180deg, #d9f0fb 0%, #c6e8f8 100%);
    display: flex;
    align-items: center;
    justify-content: center;
    gap: 32px;
    font-size: 24px;
    color: var(--ink-grey);
  }
  .contact-item {
    display: flex;
    align-items: center;
    gap: 12px;
    white-space: nowrap;
  }
  .contact-item svg { width: 26px; height: 26px; flex: none; }
</style>
</head>
<body>
  <main class="business-card">
    <div class="tree-artwork" role="img" aria-label="Illustration of a woman's silhouette as a tree trunk with a heart-shaped canopy of green leaves, flowers and butterflies, and roots below"></div>

    <header class="identity">
      <div class="person-name">Meg Donlan</div>
      <div class="person-role">Facilitator</div>
    </header>

    <h1 class="tagline">Riverbend Circle<span class="line-two">Gatherings Collective</span></h1>

    <div class="footer-band"></div>
    <footer class="contact-tab">
      <span class="contact-item">
        <svg viewBox="0 0 26 26" aria-hidden="true">
          <circle cx="13" cy="13" r="12" fill="var(--icon-blue)"/>
          <path d="M9 7.5c.6-.5 1.4-.4 1.8.2l1 1.6c.3.5.2 1.1-.2 1.5l-.7.6c.6 1.4 1.6 2.5 3 3.2l.6-.7c.4-.4 1-.5 1.5-.2l1.6 1c.6.4.7 1.2.2 1.8l-.7.8c-.6.6-1.5.8-2.3.5-3.2-1.2-5.600-3.7-6.700-6.900-.3-.8-.1-1.7.5-2.3z" fill="#fff"/>
        </svg>
        0431 582 917
      </span>
      <span class="contact-item">
        <svg viewBox="0 0 26 26" aria-hidden="true">
          <circle cx="13" cy="13" r="12" fill="var(--icon-blue)"/>
          <rect x="7" y="8.5" width="12" height="9" rx="1.2" fill="#fff"/>
          <path d="M7.5 9.2 13 13.4l5.5-4.2" fill="none" stroke="var(--icon-blue)" stroke-width="1.3"/>
        </svg>
        hi.meg.donlan@larkmail.example
      </span>
    </footer>
  </main>
</body>
</html>
```